Tech business card design

We need an amazing business card design for our new business 'Pexla' a marketing tech startup based in Sydney, Australia. We provide an online marketplace for businesses to search and buy advertising media, connect with service providers and learn more about marketing. We wish to communicate 'cool tech', reliability and professionalism and design based around our logo.

Target Market(s)

Business Owners

Contact Information for Business Card

Name
Position
Email Address
Website
Phone Number

Font styles to use
Other font styles liked:
• Avenir & Avenir Next

Colors

Designer to choose colors to be used in the design.

```html
<!DOCTYPE html>
<html lang="en">
<head>
<meta charset="utf-8">
<title>Pexla Business Card</title>
<link rel="stylesheet" href="https://fonts.googleapis.com/css2?family=Nunito+Sans:wght@400;700;800;900&display=swap">
<style>
  :root {
    --stage: #1c1c1e;
    --card-white: #ffffff;
    --card-grey: #6d6e70;
    --navy: #1b1e45;
    --ink: #2a2a2e;
    --rule: #9a9a9e;
    --band-grey: #6d6e70;
  }
  * { box-sizing: border-box; margin: 0; padding: 0; }
  html, body {
    width: 1200px;
    height: 803px;
    overflow: hidden;
    background: var(--stage);
    font-family: "Nunito Sans", Arial, sans-serif;
  }
  .stage {
    position: relative;
    width: 1200px;
    height: 803px;
    display: flex;
    align-items: center;
    justify-content: center;
    gap: 40px;
  }
  .card {
    position: relative;
    width: 520px;
    height: 297px;
    overflow: hidden;
    box-shadow: 0 10px 28px rgba(0, 0, 0, 0.55);
  }
  /* Front */
  .card--front { background: var(--card-white); }
  .card__wordmark {
    position: absolute;
    left: 34px;
    top: 96px;
    font-weight: 900;
    font-size: 96px;
    line-height: 1;
    letter-spacing: -2px;
    color: var(--navy);
  }
  .card__divider {
    position: absolute;
    left: 302px;
    top: 40px;
    width: 1px;
    height: 150px;
    background: var(--rule);
  }
  .contact {
    position: absolute;
    left: 318px;
    top: 40px;
    color: var(--ink);
    font-size: 12.5px;
    line-height: 1.35;
  }
  .contact__name {
    font-weight: 900;
    font-size: 15px;
    color: var(--navy);
    letter-spacing: 0.3px;
  }
  .contact__position {
    font-weight: 800;
    font-size: 12px;
    color: var(--ink);
    margin-bottom: 10px;
  }
  .contact__address { margin-bottom: 6px; }
  .contact__line {
    display: flex;
    align-items: center;
    gap: 5px;
  }
  .contact__icon { width: 11px; height: 11px; flex: none; }
  .card__bands {
    position: absolute;
    left: 0;
    bottom: 0;
    width: 520px;
    height: 30px;
  }
  /* Back */
  .card--back {
    background: var(--card-grey);
    display: flex;
    align-items: center;
    justify-content: center;
  }
  .card__wordmark--back {
    position: static;
    font-size: 104px;
  }
</style>
</head>
<body>
<main class="stage">
  <section class="card card--front" aria-label="Business card front">
    <div class="card__wordmark">pexla</div>
    <div class="card__divider"></div>
    <div class="contact">
      <div class="contact__name">JOHN SMITH</div>
      <div class="contact__position">Position</div>
      <div class="contact__address">Street Name, City Name<br>Zipcode:012345</div>
      <div class="contact__line">
        <svg class="contact__icon" viewBox="0 0 24 24" aria-hidden="true"><path fill="#2a2a2e" d="M6.6 10.8a15.1 15.1 0 0 0 6.6 6.6l2.2-2.2c.3-.3.7-.4 1-.2 1.1.4 2.3.6 3.6.6.6 0 1 .4 1 1V20c0 .6-.4 1-1 1C10.6 21 3 13.4 3 4c0-.6.4-1 1-1h3.5c.6 0 1 .4 1 1 0 1.3.2 2.5.6 3.6.1.3 0 .7-.2 1z"/></svg>
        <span>012-345-6789</span>
      </div>
      <div class="contact__line">
        <svg class="contact__icon" viewBox="0 0 24 24" aria-hidden="true"><rect x="2" y="5" width="20" height="14" fill="none" stroke="#2a2a2e" stroke-width="2"/><path d="M2 5l10 8 10-8" fill="none" stroke="#2a2a2e" stroke-width="2"/></svg>
        <span>info@pexla.com</span>
      </div>
      <div class="contact__line">
        <svg class="contact__icon" viewBox="0 0 24 24" aria-hidden="true"><g fill="none" stroke="#2a2a2e" stroke-width="2"><circle cx="12" cy="12" r="10"/><ellipse cx="12" cy="12" rx="4" ry="10"/><path d="M2 12h20"/></g></svg>
        <span>www.pexla.com</span>
      </div>
    </div>
    <svg class="card__bands" viewBox="0 0 520 30" aria-hidden="true">
      <polygon points="0,16 318,16 310,30 0,30" fill="var(--band-grey)"/>
      <polygon points="332,8 520,8 520,30 318,30" fill="var(--navy)"/>
    </svg>
  </section>

  <section class="card card--back" aria-label="Business card back">
    <div class="card__wordmark card__wordmark--back">pexla</div>
  </section>
</main>
</body>
</html>
```